Business card design Needed for new logo / Construction business, home extensions and new builds

We need a business card design using our new logo files which i will attach to this project :)

We are a small construction business specialising in home extensions, new builds and property development. We are very ambitious and would appreciate professional and elegant designs for our new business card.

Very serious about using the services on MakerQuarry and recently acquired our new logo from here :)

Please get involved, i will feedback when i can as i am very busy but can respond daily, thanks

Target Market(s)

People that want to build onto their houses, new building developments or adding too their existing property

Industry/Entity Type

Construction

Contact Information for Business Card

Renwick Tolliver Construction, Lionel Ashby (Managing Director), Tel 07822254961, email - info@renwick-tolliver, www.renwick-tolliver.co.uk

Colors

Designer to choose colors to be used in the design.

Requirements
Must have
• I like a deep grey on the back please. A lot of you have provided black from and back, try mixing things up a little. The black looks cool 😎 Thanks

```html
<!DOCTYPE html>
<html lang="en">
<head>
<meta charset="utf-8">
<title>Renwick Tolliver Construction – Business Card</title>
<link href="https://fonts.googleapis.com/css2?family=Open+Sans:wght@400;600;700&display=swap" rel="stylesheet">
<style>
  :root {
    --backdrop: #2b2b2e;
    --card-front: #1d1d20;
    --card-back: #27272a;
    --gold: #d9a62e;
    --gold-light: #f2cf6a;
    --gold-dark: #9c7418;
    --silver: #c9c9cc;
    --text-light: #f1f1f1;
    --emboss: #3a3a3e;
  }
  * { margin: 0; padding: 0; box-sizing: border-box; }
  html, body { width: 1200px; height: 780px; overflow: hidden; }
  body {
    background: var(--backdrop);
    font-family: "Open Sans", sans-serif;
    position: relative;
  }
  .card {
    position: absolute;
    top: 240px;
    width: 520px;
    height: 300px;
    border-radius: 4px;
    box-shadow: 0 14px 30px rgba(0,0,0,.45);
    overflow: hidden;
  }
  .card--front { left: 60px; background: var(--card-front); }
  .card--back { left: 620px; background: var(--card-back); }

  .brand {
    display: flex;
    align-items: center;
    gap: 10px;
  }
  .brand__mark {
    width: 14px; height: 14px;
    background: var(--gold);
  }
  .brand__name {
    font-weight: 600;
    font-size: 15px;
    letter-spacing: 1.5px;
    text-transform: uppercase;
    line-height: 1.25;
    color: var(--gold);
  }
  .card--front .brand { position: absolute; left: 40px; top: 34px; }

  .address {
    position: absolute; left: 40px; top: 100px;
    font-size: 13.5px; line-height: 1.5;
    color: var(--text-light);
  }
  .contacts {
    position: absolute; left: 40px; top: 170px;
    list-style: none;
    font-size: 13.5px; line-height: 1.65;
    color: var(--text-light);
  }
  .contacts li { display: flex; align-items: center; gap: 8px; }
  .contacts svg { width: 13px; height: 13px; flex: none; }

  .person {
    position: absolute; right: 60px; top: 150px;
    text-align: right;
  }
  .person__name {
    font-size: 30px; font-weight: 700; line-height: 1.1;
  }
  .person__first { color: var(--silver); }
  .person__last { color: var(--gold); }
  .person__role {
    font-size: 15px; color: var(--text-light); margin-top: 4px;
  }
  .gold-tab {
    position: absolute; right: 0; top: 170px;
    width: 44px; height: 64px;
  }

  .card--back .brand {
    position: absolute; inset: 0;
    justify-content: center;
  }
  .card--back .brand__mark { width: 22px; height: 22px; background: var(--emboss); }
  .card--back .brand__name {
    font-size: 22px; color: var(--emboss); letter-spacing: 2px; text-align: left;
  }
</style>
</head>
<body>

  <section class="card card--front" aria-label="Business card front">
    <div class="brand">
      <span class="brand__mark"></span>
      <span class="brand__name">Renwick Tolliver<br>Construction</span>
    </div>

    <p class="address">Hartwell Road, Linbrook<br>Ashcombe, AC4 7RN</p>

    <ul class="contacts">
      <li>
        <svg viewBox="0 0 16 16" aria-hidden="true"><path fill="var(--gold)" d="M3.6 1.5l2.3 2.3-1.3 1.9c.9 2 2.6 3.7 4.6 4.6l1.9-1.3 2.3 2.3-1.6 2.2C6.6 13.3 2.7 9.4 1.5 3.1z"/></svg>
        0782 225 4961
      </li>
      <li>
        <svg viewBox="0 0 16 16" aria-hidden="true"><circle cx="8" cy="8" r="6.5" fill="none" stroke="var(--gold)" stroke-width="1.6"/><path d="M1.5 8h13M8 1.5c-3 3.5-3 9.5 0 13M8 1.5c3 3.5 3 9.5 0 13" fill="none" stroke="var(--gold)" stroke-width="1.2"/></svg>
        info@renwick-tolliver.co.uk
      </li>
      <li>
        <svg viewBox="0 0 16 16" aria-hidden="true"><rect x="1.5" y="3.5" width="13" height="9" rx="1" fill="none" stroke="var(--gold)" stroke-width="1.6"/><path d="M1.8 4l6.2 5 6.2-5" fill="none" stroke="var(--gold)" stroke-width="1.4"/></svg>
        www.renwick-tolliver.co.uk
      </li>
    </ul>

    <div class="person">
      <p class="person__name"><span class="person__first">Lionel</span> <span class="person__last">Ashby</span></p>
      <p class="person__role">Managing Director</p>
    </div>

    <svg class="gold-tab" viewBox="0 0 44 64" aria-hidden="true">
      <defs>
        <linearGradient id="goldBand" x1="0" y1="0" x2="0" y2="1">
          <stop offset="0" stop-color="var(--gold-light)"/>
          <stop offset=".5" stop-color="var(--gold)"/>
          <stop offset="1" stop-color="var(--gold-dark)"/>
        </linearGradient>
      </defs>
      <rect x="22" y="0" width="22" height="18" fill="url(#goldBand)"/>
      <rect x="10" y="22" width="34" height="18" fill="url(#goldBand)"/>
      <rect x="0" y="44" width="44" height="20" fill="url(#goldBand)"/>
    </svg>
  </section>

  <section class="card card--back" aria-label="Business card back">
    <div class="brand">
      <span class="brand__mark"></span>
      <span class="brand__name">Renwick Tolliver<br>Construction</span>
    </div>
  </section>

</body>
</html>
```